Business Card for beauty technology startup

Design Glimora Business Card for a Beauty, based on the website identity and colors (https://www.glimora-example.com).
Glimora is a beauty tech startup that gathers helpful product info for beauty lovers and consumers (such as availability on stores, price range and product reviews) for makeup products. The card design must be young, colorful but clean, and very modern.

Target Market(s)

woman, 15-35

Industry/Entity Type

Cosmetics

Contact Information for Business Card

Full Name, address, phone

Font styles to use
Other font styles liked:
• Advent Pro

Colors
e34297
86cfc6
ffffff
5c5c5c
e8e8e8
e667a6
b2b2b2

Requirements
Must have
• One full colored side with a creative design and another with card info
• Use Color palette: #95C5C5 and/or #D38AA5
• Use fonts: Advent Pro
• Use website identity: https://www.glimora-example.com
Nice to have
• If needed extra font: Roboto

```html
<!DOCTYPE html>
<html lang="en">
<head>
<meta charset="utf-8">
<title>Glimora Business Card</title>
<link rel="stylesheet" href="https://fonts.googleapis.com/css2?family=Montserrat:wght@300;400;500;700&display=swap">
<style>
  :root {
    --backdrop: #d9d9d9;
    --card-white: #ffffff;
    --rose: #b97e98;
    --rose-pattern: #b07690;
    --rose-text: #b5728f;
    --ink: #3a3a3a;
    --ink-soft: #555555;
    --rule: #8a8a8a;
  }
  * { margin: 0; padding: 0; box-sizing: border-box; }
  html, body { width: 1200px; height: 800px; overflow: hidden; }
  body {
    background: var(--backdrop);
    font-family: "Montserrat", sans-serif;
    position: relative;
  }
  .card {
    position: absolute;
    top: 252px;
    width: 520px;
    height: 297px;
    box-shadow: 0 4px 14px rgba(0,0,0,0.18);
    overflow: hidden;
  }
  .card--front { left: 55px; background: var(--card-white); }
  .card--back { left: 625px; background: var(--rose); }

  /* front */
  .brand {
    position: absolute;
    top: 38px;
    right: 40px;
    display: flex;
    align-items: center;
    gap: 12px;
  }
  .brand__dot {
    width: 34px; height: 34px;
    border: 1.5px solid var(--rose-text);
    border-radius: 50%;
  }
  .brand__name {
    font-weight: 300;
    font-size: 28px;
    letter-spacing: 5px;
    color: var(--rose-text);
    text-transform: uppercase;
  }
  .edge-tab {
    position: absolute;
    left: 0; top: 170px;
    width: 8px; height: 24px;
    background: var(--rose);
    border-radius: 0 4px 4px 0;
  }
  .person { position: absolute; left: 72px; top: 142px; }
  .person__name {
    font-weight: 700;
    font-size: 17px;
    color: var(--rose-text);
    letter-spacing: 0.5px;
    text-transform: uppercase;
  }
  .person__role {
    font-size: 11px;
    color: var(--ink-soft);
    text-transform: uppercase;
    margin-top: 1px;
  }
  .divider {
    position: absolute;
    left: 72px; right: 38px; top: 190px;
    height: 1px;
    background: var(--rule);
  }
  .contacts {
    position: absolute;
    left: 72px; top: 202px;
    list-style: none;
  }
  .contacts li {
    display: flex; align-items: center; gap: 12px;
    font-size: 14px;
    color: var(--ink);
    line-height: 22px;
    letter-spacing: 0.3px;
  }
  .contacts svg { width: 10px; height: 10px; fill: none; stroke: var(--rose-text); stroke-width: 1.6; }
  .address {
    position: absolute;
    right: 38px; top: 204px;
    text-align: right;
    font-size: 12.5px;
    color: var(--ink);
    line-height: 18px;
    font-style: normal;
  }

  /* back */
  .back-pattern {
    position: absolute; inset: 0;
    background: radial-gradient(circle at 50% 50%, var(--rose) 0%, var(--rose-pattern) 100%);
  }
  .back-brand {
    position: absolute;
    inset: 0;
    display: flex; align-items: center; justify-content: center; gap: 16px;
  }
  .back-brand__ring {
    width: 70px; height: 70px;
    border: 3px solid var(--card-white);
    border-radius: 50%;
  }
  .back-brand__name {
    font-weight: 300;
    font-size: 40px;
    letter-spacing: 6px;
    color: var(--card-white);
    text-transform: uppercase;
  }
</style>
</head>
<body>
  <section class="card card--front">
    <div class="brand">
      <span class="brand__dot"></span>
      <span class="brand__name">Glimora</span>
    </div>
    <span class="edge-tab"></span>
    <div class="person">
      <p class="person__name">Lena Varga</p>
      <p class="person__role">Owner</p>
    </div>
    <div class="divider"></div>
    <ul class="contacts">
      <li><svg viewBox="0 0 10 10"><path d="M2 1 L4 3 L3 4.5 Q4.5 6.5 5.5 7 L7 6 L9 8 L7.5 9.3 Q3 8 0.8 2.5 Z"/></svg>555.014.2290</li>
      <li><svg viewBox="0 0 10 10"><rect x="0.8" y="2" width="8.4" height="6"/><path d="M0.8 2 L5 5.5 L9.2 2"/></svg>info@glimora-example.com</li>
      <li><svg viewBox="0 0 10 10"><circle cx="5" cy="5" r="4"/><path d="M1 5 H9 M5 1 Q2.5 5 5 9 M5 1 Q7.5 5 5 9"/></svg>www.glimora-example.com</li>
    </ul>
    <address class="address">48 Palm Row<br>Harbor City, FL 30000</address>
  </section>

  <section class="card card--back">
    <div class="back-pattern" role="img" aria-label="Faint repeating brand monogram pattern in rose tones"></div>
    <div class="back-brand">
      <span class="back-brand__ring"></span>
      <span class="back-brand__name">Glimora</span>
    </div>
  </section>
</body>
</html>
```